Business card for Luxury Portable Restroom Trailer company

We are a Luxury Portable Restroom Trailer Company Called FALCRIDGE HIRES. Based in Orange County California. We provide portable restroom trailers for events, such as, Weddings, Concerts, Charity events, Sporting events, Tournaments, Corporate events, ect. We rent and Sell the Luxury restrooms. Our colors are white, grey, and Orange. As you will see in the logo we uploaded.
There are 2 people in the company so the names and titles will change for the 3 people but card will remain the same. Here is the information for each Person: Dwight Penner CFO 555 318-0476
next Person: Leon Marchetti VP 555 318-0476
Next Person: Owen Marchetti CEO 555 318-0476
Information to include on the card: Luxury Restroom Trailers Rental and Sales. Weddings, Concerts, Charity, Sporting and Corp. Events.

```html
<!DOCTYPE html>
<html lang="en">
<head>
<meta charset="UTF-8">
<title>Falcridge Hires – Business Card</title>
<link rel="stylesheet" href="https://fonts.googleapis.com/css2?family=Montserrat:wght@400;500;700;800&display=swap">
<style>
  :root {
    --backdrop: #d2d5d5;
    --card: #fbfbfa;
    --orange: #d5501a;
    --charcoal: #2b2b2b;
    --grey: #4a4a4a;
    --rule: #8c8c8c;
  }
  * { margin: 0; padding: 0; box-sizing: border-box; }
  html, body { width: 1200px; height: 829px; overflow: hidden; }
  body {
    background: var(--backdrop);
    font-family: "Montserrat", sans-serif;
    position: relative;
  }
  .card {
    position: absolute;
    top: 266px;
    width: 520px;
    height: 297px;
    background: var(--card);
    box-shadow: 0 10px 30px rgba(0,0,0,0.12);
    overflow: hidden;
  }
  .card--contact { left: 50px; }
  .card--brand { left: 630px; }

  .wordmark {
    display: flex;
    align-items: center;
    gap: 10px;
    color: var(--charcoal);
    font-weight: 800;
    letter-spacing: 0.04em;
    white-space: nowrap;
  }
  .wordmark__square {
    background: var(--orange);
    flex: none;
  }

  /* contact side */
  .card--contact .wordmark {
    position: absolute;
    top: 52px;
    right: 34px;
    font-size: 20px;
  }
  .card--contact .wordmark__square { width: 16px; height: 16px; }
  .person {
    position: absolute;
    left: 38px;
    top: 92px;
  }
  .person__name {
    color: var(--orange);
    font-weight: 700;
    font-size: 22px;
    line-height: 1.1;
  }
  .person__title {
    color: var(--grey);
    font-size: 13px;
    margin-top: 2px;
  }
  .rule {
    position: absolute;
    left: 38px;
    right: 40px;
    top: 152px;
    height: 1px;
    background: var(--rule);
  }
  .contact-list {
    position: absolute;
    left: 38px;
    top: 166px;
    list-style: none;
  }
  .contact-list li {
    display: flex;
    align-items: center;
    gap: 9px;
    color: var(--charcoal);
    font-size: 13px;
    line-height: 22px;
  }
  .contact-list svg { width: 12px; height: 12px; flex: none; }
  .base-band {
    position: absolute;
    left: 0; bottom: 0;
    width: 100%;
    height: 14px;
  }

  /* brand side */
  .card--brand .wordmark {
    position: absolute;
    top: 96px;
    left: 0; right: 0;
    justify-content: center;
    font-size: 34px;
  }
  .card--brand .wordmark__square { width: 26px; height: 26px; }
  .tagline {
    position: absolute;
    top: 168px;
    left: 0; right: 0;
    text-align: center;
    color: var(--orange);
    font-weight: 500;
    font-size: 15px;
    letter-spacing: 0.02em;
  }
  .services {
    position: absolute;
    top: 194px;
    left: 0; right: 0;
    text-align: center;
    color: var(--grey);
    font-size: 14px;
    letter-spacing: 0.02em;
  }
</style>
</head>
<body>

<section class="card card--contact">
  <div class="wordmark"><span class="wordmark__square"></span>FALCRIDGE HIRES</div>

  <div class="person">
    <p class="person__name">Owen Marchetti</p>
    <p class="person__title">CEO</p>
  </div>

  <div class="rule"></div>

  <ul class="contact-list">
    <li>
      <svg viewBox="0 0 12 12" aria-hidden="true"><path fill="var(--orange)" d="M2.5 1l2 2-1 1.3c.6 1.4 1.8 2.6 3.2 3.2L8 6.5l2 2-1.2 1.7C4.8 9.8 2.2 7.2 1 3.2z"/></svg>
      555 318-0476
    </li>
    <li>
      <svg viewBox="0 0 12 12" aria-hidden="true"><rect x="1" y="2.5" width="10" height="7" fill="var(--orange)"/><path d="M1 2.8l5 3.6 5-3.6" fill="none" stroke="#fff" stroke-width="1"/></svg>
      owen@falcridgehires.com
    </li>
    <li>
      <svg viewBox="0 0 12 12" aria-hidden="true"><circle cx="6" cy="6" r="5" fill="var(--orange)"/><path d="M1 6h10M6 1c-2 2.6-2 7.4 0 10M6 1c2 2.6 2 7.4 0 10" fill="none" stroke="#fff" stroke-width="0.8"/></svg>
      www.falcridgehires.com
    </li>
  </ul>

  <svg class="base-band" viewBox="0 0 520 14" preserveAspectRatio="none" aria-hidden="true">
    <polygon points="0,0 248,0 238,14 0,14" fill="var(--orange)"/>
    <polygon points="252,0 520,0 520,14 242,14" fill="var(--charcoal)"/>
  </svg>
</section>

<section class="card card--brand">
  <div class="wordmark"><span class="wordmark__square"></span>FALCRIDGE HIRES</div>
  <p class="tagline">Luxury Restroom Trailers Rental and Sales</p>
  <p class="services">Weddings | Concerts | Charity | Sporting | Corp</p>
</section>

</body>
</html>
```